Varden Clinical new year card

Hi,
I would like a New Year greetings card to send to my customers.

If you need to look at our logo : www.vardenclinical.com

If you want to play with images of our device, see
quilotherapy.ca

The goal is to have a card to wish a happy new year and we look forward collaborating with them in the new year.

```html
<!DOCTYPE html>
<html lang="en">
<head>
<meta charset="utf-8">
<title>Varden Clinical – New Year Card</title>
<link href="https://fonts.googleapis.com/css2?family=Allura&family=Bodoni+Moda:wght@500&family=Playfair+Display:wght@500&family=Roboto+Condensed:wght@700&display=swap" rel="stylesheet">
<style>
  :root {
    --page: #ffffff;
    --card: #000000;
    --gold-light: #fff3a6;
    --gold-mid: #e0b53a;
    --gold-deep: #8a5a12;
    --brand-grey: #6d6e71;
    --brand-orange: #ea7424;
    --warm-haze: #3a2414;
    --spark: #c9a24a;
    --url-text: #ffffff;
  }
  * { margin: 0; padding: 0; box-sizing: border-box; }
  html, body {
    width: 1200px; height: 1200px; overflow: hidden;
    background: var(--page);
  }
  .card {
    position: absolute; left: 241px; top: 97px;
    width: 725px; height: 1012px;
    background: var(--card);
    overflow: hidden;
  }
  .photo-scene {
    position: absolute; left: 40px; top: 360px; width: 660px; height: 420px;
    background: radial-gradient(ellipse at 50% 45%, var(--warm-haze) 0%, rgba(40,22,12,0.6) 45%, rgba(0,0,0,0) 75%);
  }
  .burst {
    position: absolute; border-radius: 50%;
    background: radial-gradient(circle, rgba(201,162,74,0.55) 0%, rgba(201,162,74,0.2) 40%, rgba(0,0,0,0) 70%);
  }
  .burst--a { left: 140px; top: 20px;  width: 200px; height: 200px; }
  .burst--b { left: 330px; top: 40px;  width: 310px; height: 310px; }
  .burst--c { left: 20px;  top: 190px; width: 200px; height: 200px; }
  .burst--d { left: 10px;  top: 450px; width: 190px; height: 190px; }
  .burst--e { left: 530px; top: 380px; width: 180px; height: 180px; }
  .burst--f { left: 60px;  top: 680px; width: 320px; height: 320px; }
  .burst--g { left: 380px; top: 780px; width: 200px; height: 200px; }

  .brand {
    position: absolute; top: 72px; left: 0; width: 100%;
    display: flex; justify-content: center; align-items: center; gap: 14px;
  }
  .brand-mark { width: 38px; height: 38px; background: var(--brand-orange); }
  .brand-name {
    font-family: "Roboto Condensed", sans-serif; font-weight: 700;
    font-size: 50px; color: var(--brand-grey); letter-spacing: -0.5px;
    white-space: nowrap;
  }

  .gold {
    background: linear-gradient(180deg, var(--gold-light) 0%, var(--gold-mid) 45%, var(--gold-deep) 100%);
    -webkit-background-clip: text; background-clip: text; color: transparent;
  }
  .greeting {
    position: absolute; top: 190px; left: 0; width: 100%; text-align: center;
    font-family: "Playfair Display", serif; font-weight: 500; font-size: 66px; line-height: 1;
    white-space: nowrap;
  }
  .script {
    position: absolute; left: 0; width: 100%; text-align: center;
    font-family: "Allura", cursive; line-height: 1.2; white-space: nowrap;
  }
  .script--happy { top: 262px; font-size: 140px; }
  .script--year  { top: 440px; font-size: 125px; }
  .year-number {
    position: absolute; top: 558px; left: 0; width: 100%; text-align: center;
    font-family: "Bodoni Moda", serif; font-weight: 500; font-size: 200px; line-height: 1;
    letter-spacing: -4px; white-space: nowrap;
  }
  .device {
    position: absolute; left: 518px; top: 672px; width: 163px; height: 262px;
    border-radius: 40px;
    background: linear-gradient(160deg, #e8eaec 0%, #b9bcc0 60%, rgba(80,80,80,0.4) 100%);
  }
  .star { position: absolute; fill: var(--spark); }
  .url {
    position: absolute; top: 950px; left: 0; width: 100%; text-align: center;
    font-family: "Roboto Condensed", sans-serif; font-weight: 700; font-size: 28px;
    color: var(--url-text); white-space: nowrap;
  }
</style>
</head>
<body>
  <main class="card">
    <div class="photo-scene" role="img" aria-label="Softly lit photo of two people using the therapy device"></div>
    <div class="burst burst--a" role="img" aria-label="Gold firework burst"></div>
    <div class="burst burst--b" role="img" aria-label="Gold firework burst"></div>
    <div class="burst burst--c" role="img" aria-label="Gold firework burst"></div>
    <div class="burst burst--d" role="img" aria-label="Gold firework burst"></div>
    <div class="burst burst--e" role="img" aria-label="Gold firework burst"></div>
    <div class="burst burst--f" role="img" aria-label="Gold firework burst"></div>
    <div class="burst burst--g" role="img" aria-label="Gold firework burst"></div>

    <header class="brand">
      <span class="brand-mark"></span>
      <span class="brand-name">Varden Clinical</span>
    </header>

    <p class="greeting gold">Wish You a</p>
    <h1 class="script script--happy gold">Happy New</h1>
    <p class="script script--year gold">Year</p>
    <p class="year-number gold">2020</p>

    <svg class="star" style="left:394px;top:780px" width="34" height="34" viewBox="0 0 20 20" aria-hidden="true"><path d="M10 0 12 8 20 10 12 12 10 20 8 12 0 10 8 8Z"/></svg>
    <svg class="star" style="left:562px;top:400px" width="30" height="30" viewBox="0 0 20 20" aria-hidden="true"><path d="M10 0 12 8 20 10 12 12 10 20 8 12 0 10 8 8Z"/></svg>
    <svg class="star" style="left:128px;top:572px" width="28" height="28" viewBox="0 0 20 20" aria-hidden="true"><path d="M10 0 12 8 20 10 12 12 10 20 8 12 0 10 8 8Z"/></svg>

    <div class="device" role="img" aria-label="Product photo of the white neck-worn therapy device with its mouthpiece"></div>

    <p class="url">www.vardenclinical.com</p>
  </main>
</body>
</html>
```